High-Converting Facebook Ads for Portals Drapes & Louvres (6 Products)

We are looking for a graphic designer to create high-quality Facebook & Instagram ads for our business: Portals Drapes and Louvres (Melbourne, Australia).

We require 6 separate ad designs, each for a different product:

Zipscreen Blinds

Outdoor Awnings

Plantation Shutters

Roller Shutters

Security Doors

Roller Blinds & Sheer Curtains

Ad Specifications:

Sizes:

1440 x 1800 px (4:5 ratio)

1080 x 1080 px (1:1 ratio)

1080 x 1920 px (9:16 ratio for Stories/Reels)

Format: PNG (high resolution, not blurry)

Designed specifically for Meta (Facebook/Instagram ads)

Mobile-friendly layout (clear, easy to read)

Style:

Bold, sales-driven, retail-style ads (NOT minimal)

Eye-catching and designed to generate leads

Clean, professional layout

Similar to promotional home improvement ads

Brand Colours:

Red: #E31E24

Blue: #0072BC

White backgrounds

Each ad must include:

“SALE NOW ON” banner at top

Our showroom address:
482 Upper Wattleby Road, Kestrel Heights (must be fully visible, not cut off)

Phone number: 9471 2658

Our logo (provided)

Badge: “Celebrating 13 YEARS in Business” (must be clean and readable)

Call to Action:

For 5 ads: “Book a FREE quote TODAY!”

For Security Doors ad: “ORDER NOW”

Offers / Pricing:

Most products: “UP TO 40% OFF”

Plantation Shutters: “FROM $299/sqm”

Security Doors: “FROM $750”

Content for each ad (examples):

Zipscreen Blinds:

Made to Measure

Fully Installed

Wind, Sun & Insect Protection

Outdoor Awnings:

Reduce Heat & Glare

Energy Saving

Custom Made

Plantation Shutters:

Modern & Elegant

Light & Privacy Control

Durable & Easy Care

Roller Shutters:

Security Protection

Block Heat & Noise

Total Light Control

Security Doors:

3 Point Locking

Premium Mesh

Custom Made

Blinds & Sheers:

Huge Range of Fabrics

Modern Soft Finish

Perfect for Any Room

Important Notes:

All text must be sharp and easy to read (no blur)

Layout must be balanced and not overcrowded

Ensure no text is cut off (especially address and headings)

Badge text must be straight and professional (no distortion)

Use high-quality, relevant images (we will provide references)

Goal:
Create ads that look professional, trustworthy, and generate enquiries/bookings for in-home quotes.

We are open to creative ideas but want a strong, bold retail-style ad that converts.
I have uploaed chatgpt mocks

Target Market(s)

Homeowners in Melbourne, Australia (typically aged 30–65) looking to improve their homes with blinds, shutters, awnings and security doors. Mid to high income households focused on quality, security, and modern home upgrades.

Industry/Entity Type

Home Improvement / Construction / Retail

Font styles to use
Sans Serif

Requirements
Must have
• Clear, bold and easy-to-read text (must be readable on mobile) High-quality, non-blurry design Strong “SALE” style layout (retail promotional look) Proper spacing (no overcrowded designs) All key info visible (address must NOT be cut off) Correct pricing and offers included Clean “13 YEARS” badge (no distortion or curved text) Consistent branding across all 6 ads
Nice to have
• Modern, slightly premium feel while still being bold Good use of contrast (red/blue/white) Subtle shadows or layering to improve depth Clean use of icons or bullet points Strong hierarchy (headline → benefits → offer → CTA) Variations in layout for testing different ad styles
Should not have
• Minimal or plain designs (we want bold, sales-driven ads) Hard-to-read fonts or script fonts Low-quality or blurry images Overcrowded layouts with too much text Important text cut off (especially address or headings) Overuse of effects or “cheap” looking graphics Yellow-heavy colour schemes (must follow brand colours)

```html
<!DOCTYPE html>
<html lang="en">
<head>
<meta charset="utf-8">
<title>Portals Drapes &amp; Louvres – Sale Ads</title>
<link rel="stylesheet" href="https://fonts.googleapis.com/css2?family=Poppins:wght@600;800;900&family=Oswald:wght@600;700&family=Inter:wght@500;600;700&display=swap">
<style>
  :root{
    --red:#E31E24;
    --blue:#0072BC;
    --navy:#0B3F8F;
    --white:#ffffff;
    --ink:#1a1a1a;
  }
  *{box-sizing:border-box;margin:0;padding:0}
  html,body{width:1177px;height:1200px;overflow:hidden;background:var(--white)}
  .canvas{position:relative;width:1177px;height:1200px;background:var(--white)}

  .ad{position:absolute;width:300px;height:534px;background:var(--white);overflow:hidden;font-family:"Inter",sans-serif}

  .hero{position:absolute;left:0;top:0;width:300px;height:140px;background:var(--red);color:var(--white);text-align:center;font-family:"Poppins",sans-serif}
  .hero-sale{position:absolute;left:0;right:0;top:2px;font-weight:900;font-size:92px;line-height:1;letter-spacing:-2px}
  .hero-now{position:absolute;left:0;right:0;top:78px;font-weight:800;font-size:56px;line-height:1;letter-spacing:-1.5px}

  .product-band{position:absolute;left:0;top:142px;width:300px;height:43px;background:linear-gradient(90deg,var(--blue),var(--navy));color:var(--white)}
  .product-name{position:absolute;left:18px;top:1px;width:184px;font-family:"Oswald",sans-serif;font-weight:700;font-size:25px;line-height:32px;white-space:nowrap;overflow:hidden}
  .product-name.long{font-size:22px}
  .product-url{position:absolute;left:18px;top:30px;width:184px;font-size:6.4px;letter-spacing:.75px;font-weight:500;white-space:nowrap;overflow:hidden}

  .badge{position:absolute;left:212px;top:136px;width:74px;height:74px}

  .frame{position:absolute;left:118px;top:190px;width:182px;height:259px;background:var(--blue)}
  .frame-gap{position:absolute;left:131px;top:200px;width:169px;height:249px;background:var(--white)}
  .photo{position:absolute;left:135px;top:205px;width:165px;height:244px}

  .features{position:absolute;left:8px;top:190px;width:100px}
  .feature{position:absolute;left:0;width:100px;text-align:center;font-size:9px;line-height:10.5px;color:var(--ink);font-weight:500}
  .feature svg{display:block;margin:0 auto 3px;width:36px;height:36px}
  .divider{position:absolute;left:11px;width:84px;height:1px;background:#c9c9c9}

  .offer{position:absolute;left:8px;top:396px;width:108px;height:54px}
  .offer-tag{position:absolute;left:-8px;top:20px;transform:rotate(-90deg);transform-origin:center;width:44px;text-align:center;font-family:"Poppins",sans-serif;font-weight:800;font-size:11px;color:var(--blue);letter-spacing:.5px}
  .offer-value{position:absolute;left:18px;top:0;font-family:"Oswald",sans-serif;font-weight:700;color:var(--red);font-size:46px;line-height:52px;letter-spacing:-1px}
  .offer-pct{position:absolute;left:64px;top:4px;font-family:"Oswald",sans-serif;font-weight:700;color:var(--red);line-height:1;text-align:center}
  .offer-pct .pct{display:block;font-size:26px}
  .offer-pct .off{display:block;font-size:16px;margin-top:-2px}
  .offer-sub{position:absolute;left:20px;top:40px;font-family:"Poppins",sans-serif;font-weight:800;font-size:13px;color:var(--red)}

  .brand{position:absolute;left:0;top:454px;width:118px;height:80px;background:linear-gradient(90deg,#d6d6d6,#f4f4f4 60%,#ececec)}
  .brand-mark{position:absolute;left:51px;top:14px;width:16px;height:16px;background:var(--red)}
  .brand-name{position:absolute;left:0;right:0;top:36px;text-align:center;font-family:"Inter",sans-serif;font-weight:700;font-size:10px;line-height:12px;color:var(--blue)}

  .cta{position:absolute;left:118px;top:454px;width:182px;height:80px;background:var(--red)}
  .cta-line{position:absolute;left:4px;top:5px;width:178px;height:23px;background:var(--blue);color:var(--white);font-family:"Poppins",sans-serif;font-weight:600;font-size:10.5px;line-height:23px;text-align:center}
  .cta-line.order{font-size:17px;font-weight:800;letter-spacing:.3px}
  .cta-phone{position:absolute;left:4px;top:28px;width:178px;height:30px;color:var(--white);font-family:"Poppins",sans-serif;font-weight:800;font-size:21px;line-height:30px;text-align:center;letter-spacing:.5px;white-space:nowrap}
  .cta-phone svg{width:15px;height:15px;vertical-align:-1px;margin-right:5px}
  .cta-address{position:absolute;left:4px;top:58px;width:178px;height:22px;background:var(--blue);color:var(--white);font-size:6.3px;font-weight:600;line-height:22px;text-align:center;white-space:nowrap}
  .cta-address svg{width:6px;height:7px;vertical-align:-1px;margin-right:2px}
</style>
</head>
<body>
<svg width="0" height="0" style="position:absolute" aria-hidden="true">
  <defs>
    <radialGradient id="gold" cx="50%" cy="40%" r="60%">
      <stop offset="0" stop-color="#f8dd7c"/><stop offset="1" stop-color="#b8801a"/>
    </radialGradient>
    <symbol id="icon-ring" viewBox="0 0 36 36">
      <circle cx="18" cy="18" r="17" fill="#fff" stroke="#E31E24" stroke-width="1.6"/>
      <circle cx="18" cy="18" r="14" fill="#0072BC"/>
    </symbol>
    <symbol id="g-layers" viewBox="0 0 36 36"><path d="M18 10l9 4-9 4-9-4z M9 18l9 4 9-4 M9 22l9 4 9-4" fill="none" stroke="#fff" stroke-width="1.6" stroke-linejoin="round"/></symbol>
    <symbol id="g-lock" viewBox="0 0 36 36"><rect x="12" y="17" width="12" height="10" rx="1.5" fill="#fff"/><path d="M14 17v-3a4 4 0 0 1 8 0v3" fill="none" stroke="#fff" stroke-width="1.8"/></symbol>
    <symbol id="g-shield" viewBox="0 0 36 36"><path d="M18 9l8 3v6c0 5-4 8-8 9-4-1-8-4-8-9v-6z" fill="none" stroke="#fff" stroke-width="1.8"/><path d="M14.5 18l2.5 2.5 4.5-5" fill="none" stroke="#fff" stroke-width="1.6"/></symbol>
    <symbol id="g-tools" viewBox="0 0 36 36"><path d="M11 11l14 14 M25 11L11 25" stroke="#fff" stroke-width="2.2" stroke-linecap="round"/></symbol>
    <symbol id="g-mesh" viewBox="0 0 36 36"><path d="M10 12h16M10 16h16M10 20h16M10 24h16M12 10v16M16 10v16M20 10v16M24 10v16" stroke="#fff" stroke-width="1"/></symbol>
    <symbol id="g-ruler" viewBox="0 0 36 36"><rect x="9" y="15" width="18" height="6" rx="1" transform="rotate(-45 18 18)" fill="none" stroke="#fff" stroke-width="1.6"/></symbol>
    <symbol id="g-home" viewBox="0 0 36 36"><path d="M10 18l8-7 8 7v8H10z" fill="none" stroke="#fff" stroke-width="1.7" stroke-linejoin="round"/><rect x="15" y="20" width="6" height="6" fill="#fff"/></symbol>
    <symbol id="g-sun" viewBox="0 0 36 36"><circle cx="18" cy="18" r="4.5" fill="#fff"/><path d="M18 9v3M18 24v3M9 18h3M24 18h3M12 12l2 2M22 22l2 2M24 12l-2 2M12 24l2-2" stroke="#fff" stroke-width="1.5" stroke-linecap="round"/></symbol>
    <symbol id="g-drop" viewBox="0 0 36 36"><path d="M18 9c4 5 6 8 6 11a6 6 0 0 1-12 0c0-3 2-6 6-11z" fill="#fff"/></symbol>
    <symbol id="g-diamond" viewBox="0 0 36 36"><path d="M11 15l3-4h8l3 4-7 10z" fill="none" stroke="#fff" stroke-width="1.7" stroke-linejoin="round"/></symbol>
    <symbol id="g-thermo" viewBox="0 0 36 36"><rect x="16" y="9" width="4" height="12" rx="2" fill="none" stroke="#fff" stroke-width="1.5"/><circle cx="18" cy="24" r="3.5" fill="#fff"/></symbol>
    <symbol id="g-bulb" viewBox="0 0 36 36"><circle cx="18" cy="16" r="5.5" fill="none" stroke="#fff" stroke-width="1.7"/><path d="M15.5 23h5M16 26h4" stroke="#fff" stroke-width="1.6" stroke-linecap="round"/></symbol>
    <symbol id="g-link" viewBox="0 0 36 36"><circle cx="15" cy="20" r="4" fill="none" stroke="#fff" stroke-width="1.7"/><circle cx="21" cy="16" r="4" fill="none" stroke="#fff" stroke-width="1.7"/></symbol>
    <symbol id="phone" viewBox="0 0 16 16"><circle cx="8" cy="8" r="7.3" fill="none" stroke="#fff" stroke-width="1.4"/><path d="M5.3 4.6c.5-.4 1-.3 1.3.2l.6 1.2c.2.4 0 .8-.3 1l-.4.3c.4.9 1.1 1.7 2 2.1l.3-.4c.3-.3.7-.4 1-.2l1.2.6c.5.3.6.8.2 1.3-.6.7-1.5 1-2.4.6-2-.9-3.5-2.4-4.3-4.4-.3-.9 0-1.7.8-2.3z" fill="#fff"/></symbol>
    <symbol id="pin" viewBox="0 0 8 10"><path d="M4 0a3 3 0 0 1 3 3c0 2-3 5-3 5S1 5 1 3a3 3 0 0 1 3-3z" fill="#fff"/><path d="M0 9.5h8" stroke="#fff"/></symbol>
    <symbol id="badge" viewBox="0 0 74 74">
      <circle cx="37" cy="37" r="35" fill="url(#gold)"/>
      <circle cx="37" cy="37" r="31" fill="none" stroke="#8a5a10" stroke-width="1"/>
      <circle cx="37" cy="37" r="25" fill="#1b1b1b" stroke="#f5d36a" stroke-width="1.5"/>
      <text x="37" y="29" text-anchor="middle" font-family="Inter,sans-serif" font-weight="700" font-size="5" fill="#f5d36a" letter-spacing=".4">CELEBRATING</text>
      <text x="37" y="42" text-anchor="middle" font-family="Oswald,sans-serif" font-weight="600" font-size="12" fill="#ffffff">13 YEARS</text>
      <text x="37" y="50" text-anchor="middle" font-family="Inter,sans-serif" font-weight="700" font-size="5" fill="#f5d36a" letter-spacing=".4">IN BUSINESS</text>
    </symbol>
  </defs>
</svg>

<main class="canvas">

  <!-- Blinds & Sheers -->
  <section class="ad" style="left:53px;top:60px">
    <header class="hero"><div class="hero-sale">SALE</div><div class="hero-now">NOW ON</div></header>
    <div class="product-band"><div class="product-name">Blinds &amp; Sheers</div><div class="product-url">www.portalsdrapesandlouvres.com.au</div></div>
    <div class="frame"></div><div class="frame-gap"></div>
    <div class="photo" role="img" aria-label="Bedroom with grey blinds and sheer curtains over a window" style="background:linear-gradient(180deg,#e8e6e2 0%,#a9a7a3 45%,#c9a9a0 75%,#2a2626 100%)"></div>
    <svg class="badge" viewBox="0 0 74 74"><use href="#badge"/></svg>
    <div class="features">
      <div class="feature" style="top:0"><svg viewBox="0 0 36 36"><use href="#icon-ring"/><use href="#g-layers"/></svg>Huge Range<br>of Fabrics</div>
      <div class="divider" style="top:65px"></div>
      <div class="feature" style="top:69px"><svg viewBox="0 0 36 36"><use href="#icon-ring"/><use href="#g-drop"/></svg>Modern<br>Soft Finish</div>
      <div class="divider" style="top:134px"></div>
      <div class="feature" style="top:138px"><svg viewBox="0 0 36 36"><use href="#icon-ring"/><use href="#g-home"/></svg>Perfect for<br>Any Room</div>
    </div>
    <div class="offer"><div class="offer-tag">UP TO</div><div class="offer-value">40</div><div class="offer-pct"><span class="pct">%</span><span class="off">OFF</span></div></div>
    <div class="brand"><div class="brand-mark"></div><div class="brand-name">Portals Drapes<br>&amp; Louvres</div></div>
    <div class="cta"><div class="cta-line">Book a FREE quote TODAY!</div><div class="cta-phone"><svg viewBox="0 0 16 16"><use href="#phone"/></svg>9471 2658</div><div class="cta-address"><svg viewBox="0 0 8 10"><use href="#pin"/></svg>482 Upper Wattleby Road, Kestrel Heights</div></div>
  </section>

  <!-- Zipscreen Blinds -->
  <section class="ad" style="left:425px;top:60px">
    <header class="hero"><div class="hero-sale">SALE</div><div class="hero-now">NOW ON</div></header>
    <div class="product-band"><div class="product-name">Zipscreen Blinds</div><div class="product-url">www.portalsdrapesandlouvres.com.au</div></div>
    <div class="frame"></div><div class="frame-gap"></div>
    <div class="photo" role="img" aria-label="Covered outdoor patio with zipscreen blinds, ceiling fan and garden view" style="background:linear-gradient(180deg,#d9d6d0 0%,#8c8a84 35%,#6f8f4a 60%,#3a3430 100%)"></div>
    <svg class="badge" viewBox="0 0 74 74"><use href="#badge"/></svg>
    <div class="features">
      <div class="feature" style="top:0"><svg viewBox="0 0 36 36"><use href="#icon-ring"/><use href="#g-ruler"/></svg>Made to<br>Measure</div>
      <div class="divider" style="top:65px"></div>
      <div class="feature" style="top:69px"><svg viewBox="0 0 36 36"><use href="#icon-ring"/><use href="#g-tools"/></svg>Fully<br>Installed</div>
      <div class="divider" style="top:134px"></div>
      <div class="feature" style="top:138px"><svg viewBox="0 0 36 36"><use href="#icon-ring"/><use href="#g-shield"/></svg>Wind, Sun &amp;<br>Insect Protection</div>
    </div>
    <div class="offer"><div class="offer-tag">UP TO</div><div class="offer-value">40</div><div class="offer-pct"><span class="pct">%</span><span class="off">OFF</span></div></div>
    <div class="brand"><div class="brand-mark"></div><div class="brand-name">Portals Drapes<br>&amp; Louvres</div></div>
    <div class="cta"><div class="cta-line">Book a FREE quote TODAY!</div><div class="cta-phone"><svg viewBox="0 0 16 16"><use href="#phone"/></svg>9471 2658</div><div class="cta-address"><svg viewBox="0 0 8 10"><use href="#pin"/></svg>482 Upper Wattleby Road, Kestrel Heights</div></div>
  </section>

  <!-- Security Doors -->
  <section class="ad" style="left:793px;top:60px">
    <header class="hero"><div class="hero-sale">SALE</div><div class="hero-now">NOW ON</div></header>
    <div class="product-band"><div class="product-name">Security Doors</div><div class="product-url">www.portalsdrapesandlouvres.com.au</div></div>
    <div class="frame"></div><div class="frame-gap"></div>
    <div class="photo" role="img" aria-label="Home entrance at dusk with a black security door and timber surround" style="background:linear-gradient(180deg,#3c4a66 0%,#8a6a4a 40%,#c0884a 70%,#6a5040 100%)"></div>
    <svg class="badge" viewBox="0 0 74 74"><use href="#badge"/></svg>
    <div class="features">
      <div class="feature" style="top:0"><svg viewBox="0 0 36 36"><use href="#icon-ring"/><use href="#g-lock"/></svg>3 Point<br>Locking</div>
      <div class="divider" style="top:65px"></div>
      <div class="feature" style="top:69px"><svg viewBox="0 0 36 36"><use href="#icon-ring"/><use href="#g-mesh"/></svg>Premium<br>Mesh</div>
      <div class="divider" style="top:134px"></div>
      <div class="feature" style="top:138px"><svg viewBox="0 0 36 36"><use href="#icon-ring"/><use href="#g-ruler"/></svg>Custom<br>Made</div>
    </div>
    <div class="offer"><div class="offer-tag">FROM</div><div class="offer-value" style="font-size:42px">$750</div></div>
    <div class="brand"><div class="brand-mark"></div><div class="brand-name">Portals Drapes<br>&amp; Louvres</div></div>
    <div class="cta"><div class="cta-line order">ORDER NOW</div><div class="cta-phone"><svg viewBox="0 0 16 16"><use href="#phone"/></svg>9471 2658</div><div class="cta-address"><svg viewBox="0 0 8 10"><use href="#pin"/></svg>482 Upper Wattleby Road, Kestrel Heights</div></div>
  </section>

  <!-- Roller Shutters -->
  <section class="ad" style="left:53px;top:650px">
    <header class="hero"><div class="hero-sale">SALE</div><div class="hero-now">NOW ON</div></header>
    <div class="product-band"><div class="product-name">Roller Shutters</div><div class="product-url">www.portalsdrapesandlouvres.com.au</div></div>
    <div class="frame"></div><div class="frame-gap"></div>
    <div class="photo" role="img" aria-label="Dark grey roller shutter over a window on a brick house" style="background:linear-gradient(180deg,#d8d8d8 0%,#4a4a4a 30%,#2e2e2e 70%,#b07a4a 100%)"></div>
    <svg class="badge" viewBox="0 0 74 74"><use href="#badge"/></svg>
    <div class="features">
      <div class="feature" style="top:0"><svg viewBox="0 0 36 36"><use href="#icon-ring"/><use href="#g-shield"/></svg>Security<br>Protection</div>
      <div class="divider" style="top:65px"></div>
      <div class="feature" style="top:69px"><svg viewBox="0 0 36 36"><use href="#icon-ring"/><use href="#g-home"/></svg>Block<br>Heat &amp; Noise</div>
      <div class="divider" style="top:134px"></div>
      <div class="feature" style="top:138px"><svg viewBox="0 0 36 36"><use href="#icon-ring"/><use href="#g-bulb"/></svg>Total<br>Light Control</div>
    </div>
    <div class="offer"><div class="offer-tag">UP TO</div><div class="offer-value">40</div><div class="offer-pct"><span class="pct">%</span><span class="off">OFF</span></div></div>
    <div class="brand"><div class="brand-mark"></div><div class="brand-name">Portals Drapes<br>&amp; Louvres</div></div>
    <div class="cta"><div class="cta-line">Book a FREE quote TODAY!</div><div class="cta-phone"><svg viewBox="0 0 16 16"><use href="#phone"/></svg>9471 2658</div><div class="cta-address"><svg viewBox="0 0 8 10"><use href="#pin"/></svg>482 Upper Wattleby Road, Kestrel Heights</div></div>
  </section>

  <!-- Plantation Shutters -->
  <section class="ad" style="left:425px;top:650px">
    <header class="hero"><div class="hero-sale">SALE</div><div class="hero-now">NOW ON</div></header>
    <div class="product-band"><div class="product-name long">Plantation Shutters</div><div class="product-url">www.portalsdrapesandlouvres.com.au</div></div>
    <div class="frame"></div><div class="frame-gap"></div>
    <div class="photo" role="img" aria-label="Bright bedroom with white plantation shutters and timber floor" style="background:linear-gradient(180deg,#eef0f2 0%,#c8ccd0 40%,#8a8d92 65%,#8a5a34 100%)"></div>
    <svg class="badge" viewBox="0 0 74 74"><use href="#badge"/></svg>
    <div class="features">
      <div class="feature" style="top:0"><svg viewBox="0 0 36 36"><use href="#icon-ring"/><use href="#g-diamond"/></svg>Modern<br>&amp; Elegant</div>
      <div class="divider" style="top:65px"></div>
      <div class="feature" style="top:69px"><svg viewBox="0 0 36 36"><use href="#icon-ring"/><use href="#g-sun"/></svg>Light &amp;<br>Privacy Control</div>
      <div class="divider" style="top:134px"></div>
      <div class="feature" style="top:138px"><svg viewBox="0 0 36 36"><use href="#icon-ring"/><use href="#g-link"/></svg>Durable<br>&amp; Easy Care</div>
    </div>
    <div class="offer"><div class="offer-tag">FROM</div><div class="offer-value" style="font-size:36px;line-height:42px">$299</div><div class="offer-sub">PER SQM</div></div>
    <div class="brand"><div class="brand-mark"></div><div class="brand-name">Portals Drapes<br>&amp; Louvres</div></div>
    <div class="cta"><div class="cta-line">Book a FREE quote TODAY!</div><div class="cta-phone"><svg viewBox="0 0 16 16"><use href="#phone"/></svg>9471 2658</div><div class="cta-address"><svg viewBox="0 0 8 10"><use href="#pin"/></svg>482 Upper Wattleby Road, Kestrel Heights</div></div>
  </section>

  <!-- Outdoor Awnings -->
  <section class="ad" style="left:797px;top:650px">
    <header class="hero"><div class="hero-sale">SALE</div><div class="hero-now">NOW ON</div></header>
    <div class="product-band"><div class="product-name">Outdoor Awnings</div><div class="product-url">www.portalsdrapesandlouvres.com.au</div></div>
    <div class="frame"></div><div class="frame-gap"></div>
    <div class="photo" role="img" aria-label="Green and white striped awning over a window on a red brick wall" style="background:linear-gradient(180deg,#f2f2f2 0%,#3f6a4e 25%,#4f7a5e 45%,#a4533a 70%,#8e4532 100%)"></div>
    <svg class="badge" viewBox="0 0 74 74"><use href="#badge"/></svg>
    <div class="features">
      <div class="feature" style="top:0"><svg viewBox="0 0 36 36"><use href="#icon-ring"/><use href="#g-thermo"/></svg>Reduce<br>Heat &amp; Glare</div>
      <div class="divider" style="top:65px"></div>
      <div class="feature" style="top:69px"><svg viewBox="0 0 36 36"><use href="#icon-ring"/><use href="#g-bulb"/></svg>Energy<br>Saving</div>
      <div class="divider" style="top:134px"></div>
      <div class="feature" style="top:138px"><svg viewBox="0 0 36 36"><use href="#icon-ring"/><use href="#g-ruler"/></svg>Custom<br>Made</div>
    </div>
    <div class="offer"><div class="offer-tag">UP TO</div><div class="offer-value">40</div><div class="offer-pct"><span class="pct">%</span><span class="off">OFF</span></div></div>
    <div class="brand"><div class="brand-mark"></div><div class="brand-name">Portals Drapes<br>&amp; Louvres</div></div>
    <div class="cta"><div class="cta-line">Book a FREE quote TODAY!</div><div class="cta-phone"><svg viewBox="0 0 16 16"><use href="#phone"/></svg>9471 2658</div><div class="cta-address"><svg viewBox="0 0 8 10"><use href="#pin"/></svg>482 Upper Wattleby Road, Kestrel Heights</div></div>
  </section>

</main>
</body>
</html>
```